Business Cards for a law firm

Business cards for our law firm. Use our silhoette logo and OAK PARTNERS - check our website (www.oakpartners.example)

Contact Information for Business Card

our silhouette logo, OAK PARTNERS, 800-555-0147, Dorian Pemberton, dorian@oakpartners.example

Requirements
Must have
• our silhouette logo, OAK PARTNERS, 800-555-0147, Dorian Pemberton, dorian@oakpartners.example

```html
<!DOCTYPE html>
<html lang="en">
<head>
<meta charset="utf-8">
<title>Oak Partners – Business Cards</title>
<link href="https://fonts.googleapis.com/css2?family=Montserrat:wght@400;500;700&display=swap" rel="stylesheet">
<style>
  :root {
    --navy: #23346b;
    --paper: #ffffff;
    --backdrop: #dfe5e8;
  }
  * { box-sizing: border-box; margin: 0; padding: 0; }
  html, body { width: 1200px; height: 960px; overflow: hidden; }
  body {
    background: var(--backdrop);
    font-family: "Montserrat", Arial, sans-serif;
    position: relative;
  }
  .card {
    position: absolute;
    left: 246px;
    width: 708px;
    height: 404px;
    overflow: hidden;
  }
  .card-front { top: 58px; background: var(--navy); color: var(--paper); }
  .card-back  { top: 498px; background: var(--paper); color: var(--navy); }

  .brand {
    position: absolute;
    display: flex;
    align-items: center;
    gap: 22px;
  }
  .brand-mark { display: block; flex: none; }
  .brand-name {
    font-weight: 400;
    letter-spacing: 0.04em;
    line-height: 1.05;
    text-transform: uppercase;
  }
  .card-front .brand { left: 108px; top: 120px; }
  .card-front .brand-mark { width: 104px; height: 104px; background: var(--paper); }
  .card-front .brand-name { font-size: 44px; }

  .card-back .brand { left: 176px; top: 30px; }
  .card-back .brand-mark { width: 80px; height: 80px; background: var(--navy); }
  .card-back .brand-name { font-size: 34px; }

  .holder {
    position: absolute;
    left: 19px;
    top: 252px;
    font-size: 22px;
    letter-spacing: 0.05em;
    text-transform: uppercase;
  }
  .holder-first { font-weight: 700; }
  .holder-last { font-weight: 400; }

  .divider {
    position: absolute;
    left: 351px;
    top: 208px;
    width: 1px;
    height: 117px;
    background: var(--navy);
  }

  .contact-list {
    position: absolute;
    left: 387px;
    top: 244px;
    list-style: none;
  }
  .contact-item {
    display: flex;
    align-items: center;
    gap: 10px;
    font-size: 14px;
    letter-spacing: 0.06em;
    text-transform: uppercase;
    height: 23px;
  }
  .contact-item.phone { font-size: 18px; }
  .contact-icon { width: 16px; height: 16px; fill: var(--navy); flex: none; }

  .email-band {
    position: absolute;
    left: 0;
    top: 343px;
    width: 100%;
    height: 30px;
    background: var(--navy);
    color: var(--paper);
    display: flex;
    align-items: center;
    justify-content: center;
    gap: 14px;
    padding-right: 90px;
    font-size: 15px;
    letter-spacing: 0.05em;
    text-transform: uppercase;
  }
  .email-band .contact-icon { fill: var(--paper); }

  .corner-mark {
    position: absolute;
    left: 610px;
    top: 330px;
    width: 44px;
    height: 44px;
    background: var(--navy);
  }
</style>
</head>
<body>

<section class="card card-front">
  <div class="brand">
    <span class="brand-mark"></span>
    <div class="brand-name">Oak<br>Partners</div>
  </div>
</section>

<section class="card card-back">
  <div class="brand">
    <span class="brand-mark"></span>
    <div class="brand-name">Oak<br>Partners</div>
  </div>

  <p class="holder"><span class="holder-first">Dorian</span> <span class="holder-last">Pemberton</span></p>

  <span class="divider"></span>

  <ul class="contact-list">
    <li class="contact-item phone">
      <svg class="contact-icon" viewBox="0 0 24 24" aria-hidden="true"><path d="M6.6 10.8a15.1 15.1 0 0 0 6.6 6.6l2.2-2.2a1 1 0 0 1 1-.25 11.4 11.4 0 0 0 3.6.57 1 1 0 0 1 1 1V20a1 1 0 0 1-1 1A17 17 0 0 1 3 4a1 1 0 0 1 1-1h3.5a1 1 0 0 1 1 1c0 1.25.2 2.45.57 3.57a1 1 0 0 1-.25 1z"/></svg>
      <span>800-555-0147</span>
    </li>
    <li class="contact-item web">
      <svg class="contact-icon" viewBox="0 0 24 24" aria-hidden="true"><path d="M12 2a10 10 0 1 0 0 20 10 10 0 0 0 0-20zm6.9 6h-3a15.7 15.7 0 0 0-1.4-3.6A8 8 0 0 1 18.9 8zM12 4a14 14 0 0 1 1.9 4h-3.8A14 14 0 0 1 12 4zM4.3 14a8 8 0 0 1 0-4h3.4a16 16 0 0 0 0 4zm.8 2h3a15.7 15.7 0 0 0 1.4 3.6A8 8 0 0 1 5.1 16zm3-8h-3a8 8 0 0 1 4.4-3.6A15.7 15.7 0 0 0 8.1 8zM12 20a14 14 0 0 1-1.9-4h3.8A14 14 0 0 1 12 20zm2.3-6H9.7a14.600 14.600 0 0 1 0-4h4.6a14.600 14.600 0 0 1 0 4zm.2 5.6a15.700 15.700 0 0 0 1.4-3.6h3a8 8 0 0 1-4.4 3.6zm1.8-5.6a16 16 0 0 0 0-4h3.4a8 8 0 0 1 0 4z"/></svg>
      <span>www.oakpartners.example</span>
    </li>
  </ul>

  <div class="email-band">
    <svg class="contact-icon" viewBox="0 0 24 24" aria-hidden="true"><path d="M3 5h18a1 1 0 0 1 1 1v12a1 1 0 0 1-1 1H3a1 1 0 0 1-1-1V6a1 1 0 0 1 1-1zm1 2.4V17h16V7.4l-8 5.2zM5.8 7 12 11l6.2-4z"/></svg>
    <span>dorian@oakpartners.example</span>
  </div>

  <span class="corner-mark"></span>
</section>

</body>
</html>
```